Aquatic View

We need a web design for a new window cleaning company name Tidewell Glass Care. We are located in Grand Cayman, Cayman Islands. We are a small company, a team of husband and wife. Our services include residencial interior and exterior window cleaning and commercial. Extra services such as ceiling fans cleaning, mirrors, high dusting. Home cleaning services. Power washing. Explaining the service. We want a modern, beachy style with aquatic colors. We want to use our domain name "tidewellglasscare.ky". We want to portray a clean, modern and professional design.

Target Market(s)

Big Home owners

Industry/Entity Type

Cleaning Service

Contact Information for Business Card

Company Name: Tidewell Glass Care
Name: Desmond Farrowby owner/manager
Phone: 345-9170452
Email: desmond@tidewellglasscare.ky
Website: tidewellglasscare.ky
Address: P.O.Box 2486 GT, George Town, Grand Cayman KY1-1203 Cayman Islands

Number of Pages Required

2 page

Font styles to use
Sans Serif

Colors
0592cd
0455a3
33a6d7
85cae6
cadf82
abd036
fbf289

Requirements
Nice to have
• Pictures of an ocean view and palm trees from clear windows.
• https://quorvantel.com/bidlinker/
• Use the above for "free estimate".

```html
<!DOCTYPE html>
<html lang="en">
<head>
<meta charset="utf-8">
<title>Tidewell Glass Care</title>
<link href="https://fonts.googleapis.com/css2?family=Open+Sans:wght@400;600;700&display=swap" rel="stylesheet">
<style>
:root{
  --ocean:#0592cd;
  --deep:#0455a3;
  --sky:#33a6d7;
  --mist:#85cae6;
  --lime-soft:#cadf82;
  --lime:#abd036;
  --sand:#fbf289;
  --ink:#333;
  --muted:#777;
  --line:#e3e7ea;
  --white:#fff;
}
*{box-sizing:border-box;margin:0;padding:0}
html,body{width:1200px;height:5000px;overflow:hidden}
body{font-family:"Open Sans",Arial,sans-serif;color:var(--ink);background:var(--white);font-size:14px;line-height:1.6}
.section-title{text-align:center;color:var(--ocean);font-size:38px;font-weight:400;line-height:1.2}
.section-sub{text-align:center;color:var(--muted);font-size:16px;margin-top:4px}
.read-more{font-size:12px;color:var(--ink);text-decoration:underline;display:inline-block;margin-top:8px}

/* header */
.site-header{height:100px;position:relative;background:var(--white)}
.brand{position:absolute;left:160px;top:14px;display:flex;align-items:center;gap:12px}
.brand-mark{width:40px;height:40px;border-radius:50%;background:var(--ocean)}
.brand-name{font-size:24px;font-weight:700;color:var(--deep);line-height:1}
.top-contact{position:absolute;right:160px;top:14px;font-size:12px;color:var(--muted);display:flex;gap:22px}
.main-nav{position:absolute;right:160px;top:64px;display:flex;gap:22px;font-size:13px;color:var(--ocean)}
.main-nav span+span{border-left:1px solid var(--line);padding-left:22px}

/* hero */
.hero{position:relative;height:560px}
.hero-photo{position:absolute;inset:0;background:linear-gradient(180deg,#cfe6f3 0%,#f4f8fb 45%,#e6e0d8 75%,#d3c7b8 100%)}
.hero-arrow{position:absolute;top:250px;width:26px;height:60px;background:var(--deep);display:flex;align-items:center;justify-content:center}
.hero-arrow.left{left:0}.hero-arrow.right{right:0}
.estimate-badge{position:absolute;left:500px;top:370px;width:200px;height:96px;background:var(--deep);border:3px solid var(--white);border-radius:6px;color:var(--white);text-align:center;padding-top:10px}
.estimate-badge b{display:block;font-size:34px;line-height:1;color:var(--white)}
.estimate-badge span{font-size:18px;letter-spacing:2px;font-weight:700}
.hero-caption{position:absolute;left:0;right:0;bottom:0;height:70px;background:rgba(4,85,163,.75);color:var(--white);font-size:22px;font-weight:600;text-align:center;line-height:70px}

/* about */
.about{padding:40px 160px 0;height:460px}
.about .lead{text-align:center;color:var(--ocean);font-size:15px;margin:6px 0 20px}
.about-body{display:flex;gap:24px}
.about-photo{width:200px;height:160px;flex:none;background:linear-gradient(135deg,#cfe4ef,#7fb6d6)}
.about p{font-size:12px;color:var(--muted);line-height:1.55}
.about .full{margin-top:12px}

/* services */
.services{padding:20px 0 0;height:1820px}
.service-list{margin-top:30px}
.service{position:relative;height:230px;margin:0 160px 20px;box-shadow:0 2px 8px rgba(0,0,0,.12);background:var(--white)}
.service-photo{position:absolute;top:0;width:240px;height:200px}
.service-num{position:absolute;top:80px;width:80px;height:80px;color:var(--white);font-size:38px;font-weight:600;display:flex;align-items:center;justify-content:center}
.service-text{position:absolute;top:30px;width:520px}
.service-text h3{font-size:15px;font-weight:700;margin-bottom:8px}
.service-text p{font-size:12px;color:var(--muted);line-height:1.6}
.service.left .service-photo{left:0}
.service.left .service-num{left:240px}
.service.left .service-text{left:350px}
.service.right .service-photo{right:0}
.service.right .service-num{right:240px}
.service.right .service-text{left:30px}
.bg-ocean{background:var(--ocean)}.bg-deep{background:var(--deep)}.bg-sky{background:var(--sky)}.bg-mist{background:var(--mist)}.bg-lime{background:var(--lime)}.bg-lime-soft{background:var(--lime-soft)}.bg-sand{background:var(--sand);color:var(--deep)!important}

/* consultation */
.consult{position:relative;height:720px;overflow:hidden}
.consult-scene{position:absolute;inset:0;background:linear-gradient(180deg,#0a5fa8 0%,#3e92c9 40%,#9ccbe3 70%,#3c7fb8 100%)}
.consult .section-title,.consult .section-sub{position:relative;color:var(--white);padding-top:0}
.consult .section-title{padding-top:30px}
.consult-icon{position:absolute;left:575px;top:118px;width:50px;height:50px;border:2px solid var(--white);border-radius:50%}
.consult-card{position:absolute;left:380px;top:140px;width:480px;height:480px;background:var(--white);border-radius:4px;padding:60px 50px 0}
.consult-close{position:absolute;right:-14px;top:-14px;width:30px;height:30px;border-radius:50%;background:#222;border:2px solid var(--white)}
.consult-card .intro{font-size:11px;color:var(--muted);text-align:center;margin-bottom:20px}
.field{height:34px;border:1px solid var(--line);margin-bottom:10px;font-size:11px;color:#aaa;padding:0 12px;line-height:32px;position:relative}
.field.select::after{content:"";position:absolute;right:0;top:0;width:30px;height:32px;background:var(--deep)}
.form-foot{display:flex;align-items:center;gap:18px;margin-top:8px}
.btn{background:var(--deep);color:var(--white);font-size:12px;font-weight:700;padding:8px 18px;display:inline-block}
.checks{display:flex;gap:14px;font-size:10px;color:var(--muted)}
.checks span::before{content:"";display:inline-block;width:10px;height:10px;border:1px solid #aaa;margin-right:5px;vertical-align:-1px}

/* testimonials */
.testimonials{height:500px;background:#f1f7e6;padding-top:40px;position:relative}
.client-photo{position:absolute;left:160px;top:160px;width:200px;height:200px;border-radius:50%;background:linear-gradient(135deg,#d9ecc0,#8fb878);border:6px solid var(--white)}
.quote{position:absolute;left:420px;top:180px;width:620px}
.quote-mark{color:var(--muted);font-size:40px;line-height:.5;position:absolute;left:-34px;top:10px}
.quote p{font-size:15px;color:var(--deep)}
.quote h4{margin-top:24px;color:var(--deep);font-size:17px}
.quote small{font-size:11px;color:var(--muted)}
.dots{position:absolute;left:560px;top:390px;display:flex;gap:10px}
.dots i{width:14px;height:14px;border-radius:50%;background:#9a9a9a}
.dots i:last-child{background:#555}

/* partners */
.partners{height:240px;padding-top:26px;position:relative}
.partner-row{position:absolute;left:160px;right:160px;top:110px;display:flex;justify-content:space-around;align-items:center}
.partner-badge{width:240px;height:70px;border-radius:35px}
.partner-arrow{position:absolute;top:132px;width:26px;height:26px;border-radius:50%;background:var(--lime)}
.partner-arrow.left{left:160px}.partner-arrow.right{right:160px}

/* contact */
.contact{height:560px;background:var(--deep);color:var(--white);position:relative;padding-top:40px}
.contact .section-title{color:var(--white);font-size:30px;font-weight:700}
.contact .section-sub{color:var(--mist)}
.contact-info{position:absolute;left:160px;top:150px;width:440px;font-size:13px}
.contact-info h4{font-size:14px;margin-bottom:4px}
.contact-info ul{list-style:none;margin-top:28px}
.contact-info li{display:flex;gap:12px;align-items:flex-start;margin-bottom:10px}
.contact-info svg{flex:none;margin-top:3px}
.socials{display:flex;gap:10px;margin-top:26px}
.socials i{width:26px;height:26px;border-radius:50%;background:var(--white)}
.contact-form{position:absolute;left:620px;top:230px;width:420px}
.contact-form .row{display:flex;gap:10px}
.contact-form .input{flex:1;height:34px;background:var(--white);color:#aaa;font-size:11px;padding:0 10px;line-height:34px;margin-bottom:10px}
.contact-form .area{height:130px}
.contact-form .btn{background:var(--ocean);margin:4px 0 0 150px;padding:8px 40px}
.site-footer{position:absolute;left:0;right:0;bottom:0;height:40px;background:var(--ocean);text-align:center;font-size:11px;line-height:40px;color:var(--white)}
</style>
</head>
<body>

<header class="site-header">
  <div class="brand"><span class="brand-mark"></span><span class="brand-name">Tidewell Glass Care</span></div>
  <div class="top-contact"><span>+1 345-9170452</span><span>desmond@tidewellglasscare.ky</span></div>
  <nav class="main-nav"><span>Home</span><span>About Us</span><span>Services</span><span>Free Estimate</span><span>Testimonials</span><span>Contact</span></nav>
</header>

<section class="hero">
  <div class="hero-photo" role="img" aria-label="Bright bedroom with clear windows overlooking the ocean"></div>
  <div class="hero-arrow left"><svg width="10" height="16"><path d="M8 1 2 8l6 7" stroke="#fff" stroke-width="2" fill="none"/></svg></div>
  <div class="hero-arrow right"><svg width="10" height="16"><path d="M2 1l6 7-6 7" stroke="#fff" stroke-width="2" fill="none"/></svg></div>
  <div class="estimate-badge"><b>FREE</b><span>ESTIMATE</span></div>
  <div class="hero-caption">Our Services Include Residencial Interior And Exterior Window Cleaning And Commercial</div>
</section>

<section class="about">
  <h2 class="section-title">About Us</h2>
  <p class="lead">Tidewell Glass Care, We are located in Grand Cayman, Cayman Islands</p>
  <div class="about-body">
    <div class="about-photo" role="img" aria-label="Cleaner washing a large window"></div>
    <p>We are a small company, a team of husband and wife. Our services include residencial interior and exterior window cleaning and commercial. Extra services such as ceiling fans cleaning, mirrors, high dusting, home cleaning services and power washing. Lorem Ipsum is simply dummy text of the printing and typesetting industry. Lorem Ipsum has been the industry's standard dummy text ever since the 1500s, when an unknown printer took a galley of type and scrambled it to make a type specimen book. Lorem Ipsum is simply dummy text of the printing and typesetting industry. Lorem Ipsum has been the industry's standard dummy text ever since the 1500s.</p>
  </div>
  <p class="full">Lorem Ipsum is simply dummy text of the printing and typesetting industry. Lorem Ipsum has been the industry's standard dummy text ever since the 1500s, when an unknown printer took a galley of type and scrambled it to make a type specimen book. Lorem Ipsum is simply dummy text of the printing and typesetting industry. Lorem Ipsum has been the industry's standard dummy text ever since the 1500s. Lorem Ipsum is simply dummy text of the printing and typesetting industry. Lorem Ipsum has been the industry's standard dummy text ever since the 1500s, when an unknown printer took a galley of type and scrambled it.</p>
  <span class="read-more">Read More...</span>
</section>

<section class="services">
  <h2 class="section-title">Our Services</h2>
  <p class="section-sub">Check Our Operation step by step ( how we do it )</p>
  <div class="service-list">
    <article class="service left">
      <div class="service-photo" style="background:linear-gradient(135deg,#3a6f9c,#9cc7e0)" role="img" aria-label="Worker cleaning a home window from outside"></div>
      <div class="service-num bg-sky">1</div>
      <div class="service-text"><h3>Residencial Interior And Exterior Window Cleaning</h3><p>Lorem Ipsum is simply dummy text of the printing and typesetting industry. Lorem Ipsum has been the industry's standard dummy text ever since the 1500s, when an unknown printer took a galley of type and scrambled it.</p><span class="read-more">Read More...</span></div>
    </article>
    <article class="service right">
      <div class="service-photo" style="background:linear-gradient(135deg,#1b5f9e,#6fb3dd)" role="img" aria-label="Window washer on a commercial glass facade"></div>
      <div class="service-num bg-deep">2</div>
      <div class="service-text"><h3>Commercial Window Cleaning</h3><p>Lorem Ipsum is simply dummy text of the printing and typesetting industry. Lorem Ipsum has been the industry's standard dummy text ever since the 1500s, when an unknown printer took a galley of type and scrambled it.</p><span class="read-more">Read More...</span></div>
    </article>
    <article class="service left">
      <div class="service-photo" style="background:linear-gradient(135deg,#f3e26a,#d8c14a)" role="img" aria-label="Duster cleaning a ceiling fan"></div>
      <div class="service-num bg-mist">3</div>
      <div class="service-text"><h3>Ceiling Fans Cleaning</h3><p>Lorem Ipsum is simply dummy text of the printing and typesetting industry. Lorem Ipsum has been the industry's standard dummy text ever since the 1500s, when an unknown printer took a galley of type and scrambled it.</p><span class="read-more">Read More...</span></div>
    </article>
    <article class="service right">
      <div class="service-photo" style="background:linear-gradient(135deg,#cfe3ee,#6aa8cf)" role="img" aria-label="Cleaner polishing a mirror"></div>
      <div class="service-num bg-mist">4</div>
      <div class="service-text"><h3>Mirrors Cleaning</h3><p>Lorem Ipsum is simply dummy text of the printing and typesetting industry. Lorem Ipsum has been the industry's standard dummy text ever since the 1500s, when an unknown printer took a galley of type and scrambled it.</p><span class="read-more">Read More...</span></div>
    </article>
    <article class="service left">
      <div class="service-photo" style="background:linear-gradient(135deg,#e6d7c4,#b89c7c)" role="img" aria-label="Person dusting high shelves"></div>
      <div class="service-num bg-lime-soft">5</div>
      <div class="service-text"><h3>High Dusting</h3><p>Lorem Ipsum is simply dummy text of the printing and typesetting industry. Lorem Ipsum has been the industry's standard dummy text ever since the 1500s, when an unknown printer took a galley of type and scrambled it.</p><span class="read-more">Read More...</span></div>
    </article>
    <article class="service right">
      <div class="service-photo" style="background:linear-gradient(135deg,#f2d5e6,#9fc6e2)" role="img" aria-label="Gloved hand spraying a surface in a home"></div>
      <div class="service-num bg-lime">6</div>
      <div class="service-text"><h3>Home Cleaning Services</h3><p>Lorem Ipsum is simply dummy text of the printing and typesetting industry. Lorem Ipsum has been the industry's standard dummy text ever since the 1500s, when an unknown printer took a galley of type and scrambled it.</p><span class="read-more">Read More...</span></div>
    </article>
    <article class="service left">
      <div class="service-photo" style="background:linear-gradient(135deg,#8f8a80,#c9c4b8)" role="img" aria-label="Power washing a paved driveway"></div>
      <div class="service-num bg-sand">7</div>
      <div class="service-text"><h3>Power washing</h3><p>Lorem Ipsum is simply dummy text of the printing and typesetting industry. Lorem Ipsum has been the industry's standard dummy text ever since the 1500s, when an unknown printer took a galley of type and scrambled it.</p><span class="read-more">Read More...</span></div>
    </article>
  </div>
</section>

<section class="consult">
  <div class="consult-scene" role="img" aria-label="Open white windows looking out to a sunny beach with palm trees"></div>
  <h2 class="section-title">Free Consultation</h2>
  <p class="section-sub">Enter your details below</p>
  <div class="consult-card">
    <span class="consult-close"></span>
    <p class="intro">Tidewell Glass Care, We are located in Grand Cayman, Cayman Islands. Our services include residencial interior and exterior window cleaning and commercial.</p>
    <div class="field">Name</div>
    <div class="field">Mobile number</div>
    <div class="field">Email address</div>
    <div class="field select">Select your cleaning</div>
    <div class="field select">Schedule</div>
    <div class="form-foot"><span class="btn">SUBMIT NOW</span><div class="checks"><span>MORNING</span><span>AFTERNOON</span></div></div>
  </div>
  <span class="consult-icon"><svg width="46" height="46"><path d="M14 19l9 9 9-9" stroke="#fff" stroke-width="2.5" fill="none"/></svg></span>
</section>

<section class="testimonials">
  <h2 class="section-title">Client Testimonials</h2>
  <p class="section-sub">Let me say light up there</p>
  <div class="client-photo" role="img" aria-label="Portrait of a smiling client"></div>
  <div class="quote">
    <span class="quote-mark">&#8220;</span>
    <p>Lorem Ipsum is simply dummy text of the printing and typesetting industry. Lorem Ipsum has been the industry's standard dummy text ever since the 1500s, when an unknown printer took a galley of type and scrambled.</p>
    <h4>Marisol Trent</h4>
    <small>President, Harbour Medical Consultants, Inc.</small>
  </div>
  <div class="dots"><i></i><i></i><i></i><i></i></div>
</section>

<section class="partners">
  <h2 class="section-title">Our Partner</h2>
  <span class="partner-arrow left"></span>
  <div class="partner-row">
    <span class="partner-badge" style="background:var(--deep)"></span>
    <span class="partner-badge" style="background:var(--lime)"></span>
    <span class="partner-badge" style="background:var(--sky)"></span>
  </div>
  <span class="partner-arrow right"></span>
</section>

<section class="contact">
  <h2 class="section-title">Contact</h2>
  <p class="section-sub">Let's talk business, get in touch!</p>
  <div class="contact-info">
    <h4>Office Hours</h4>
    <p>Monday to Friday / 7:00 - 18:00 Saturday / 9:00 - 13:00</p>
    <ul>
      <li><svg width="12" height="16"><path d="M6 1a5 5 0 0 0-5 5c0 4 5 9 5 9s5-5 5-9a5 5 0 0 0-5-5z" fill="#fff"/><circle cx="6" cy="6" r="2" fill="#0455a3"/></svg><span>Tidewell Glass Care, Grand Cayman, Cayman Islands</span></li>
      <li><svg width="14" height="14"><path d="M3 1l3 3-2 2c1 2 2 3 4 4l2-2 3 3-2 2C6 13 1 8 1 3z" fill="#fff"/></svg><span>+1 345-9170452</span></li>
      <li><svg width="14" height="12"><rect x="1" y="1" width="12" height="10" fill="#fff"/><path d="M1 1l6 5 6-5" stroke="#0455a3" fill="none"/></svg><span>desmond@tidewellglasscare.ky</span></li>
    </ul>
    <div class="socials"><i></i><i></i><i></i></div>
  </div>
  <div class="contact-form">
    <div class="row"><div class="input">Name</div><div class="input">Email (will not published)</div></div>
    <div class="input area">Message</div>
    <span class="btn">Send</span>
  </div>
  <footer class="site-footer">Copyright &copy; Tidewell Glass Care . All Rights Reserved.</footer>
</section>

</body>
</html>
```